A New and modern Business Card for Tarwick Trade Solutions Ltd

New and modern Logo and Business Card Attached is the current logo/business card designCurrently the business is called "Tarwick & Co." or TTS Ltd for short. This is subject to change.This business specialises in Telecoms and Energy. We work with the major networks (QV, K7, etc) and also offer Energy Products saving clients money off their energy bills.These are business to business services.The current design incorporates a Pheonix, indicating rebirth, starting something new.We would like to maintain the Phoenix element but a newer modern style.We love colours in the logo 3 max.The aim of this is to be ultra slick and modern. I envisage Tarwick & Co. on one side of the card with long descriptions on the other side.Side 1:TTS Ltd/Logo?Side 2:TTS Ltd/Logo/Graphic?Brogan & Co.Name:Address:Phone:Email:The design is mostly flexible but must incorporate a Phoenix.For example "Tarwick & Co." with a block phoenix behind the text...up to you.

Industry/Entity Type

Telecommunications

Contact Information for Business Card

Tarwick & Co.
Address:
Name:
Phone:
Email:

Logo Text

Tarwick & Co.

Colors
33a6d7
0792cd
acd037
9bcb3c
f78f20
fece3e

Requirements
Must have
• Phoenix
• 3/4 colours max
• Blue representing Technology (wireless)
• Green for Eco Energy
• Orange for Phoenix
• White business card background
Should not have
• phoenix must not all be red/ orange fire, we are a technology service company and the phoenix colours must represent this. Fire is not representative of our company.

```html
<!DOCTYPE html>
<html lang="en">
<head>
<meta charset="utf-8">
<title>Tarwick Trade Solutions Ltd – Business Card</title>
<link rel="stylesheet" href="https://fonts.googleapis.com/css2?family=Cinzel:wght@400&family=Lato:wght@400;700&display=swap">
<style>
  :root {
    --backdrop: #2a2a2a;
    --card-white: #ffffff;
    --tech-blue: #0792cd;
    --sky-blue: #33a6d7;
    --eco-green: #9bcb3c;
    --phoenix-orange: #f78f20;
    --ink: #3f3f3f;
    --rule: #5a5a5a;
  }
  * { box-sizing: border-box; margin: 0; padding: 0; }
  html, body {
    width: 1200px;
    height: 1200px;
    overflow: hidden;
    background: var(--backdrop);
  }
  .canvas {
    position: relative;
    width: 1200px;
    height: 1200px;
  }
  .card {
    position: absolute;
    top: 310px;
    height: 594px;
  }
  .card-front {
    left: 234px;
    width: 364px;
    background: var(--card-white);
    text-align: center;
    font-family: "Lato", Arial, sans-serif;
    color: var(--ink);
  }
  .card-back {
    left: 627px;
    width: 369px;
    background: var(--tech-blue);
    overflow: hidden;
  }
  .brand-mark {
    position: absolute;
    left: 132px;
    top: 105px;
    width: 100px;
    height: 100px;
    border-radius: 50%;
    background: var(--phoenix-orange);
  }
  .brand-name {
    position: absolute;
    left: 0;
    width: 100%;
    top: 240px;
    font-weight: 400;
    line-height: 1;
  }
  .brand-name .brand-main {
    display: block;
    font-family: "Cinzel", Georgia, serif;
    font-size: 50px;
    letter-spacing: 1px;
    color: var(--tech-blue);
  }
  .brand-name .brand-sub {
    display: block;
    margin-top: 8px;
    font-family: "Lato", Arial, sans-serif;
    font-weight: 700;
    font-size: 15px;
    letter-spacing: 3px;
    color: var(--eco-green);
  }
  .contact {
    position: absolute;
    left: 0;
    width: 100%;
    top: 389px;
  }
  .contact-name {
    font-size: 22px;
    color: var(--phoenix-orange);
    line-height: 26px;
  }
  .contact-role {
    font-size: 17px;
    line-height: 20px;
  }
  .contact-rule {
    width: 154px;
    height: 1px;
    background: var(--rule);
    margin: 7px auto 6px;
  }
  .contact-line {
    font-size: 17px;
    line-height: 21px;
  }
  .back-art {
    position: absolute;
    inset: 0;
  }
  .back-name {
    position: absolute;
    left: 0;
    width: 100%;
    top: 440px;
    text-align: center;
    font-family: "Cinzel", Georgia, serif;
    font-weight: 400;
    font-size: 30px;
    letter-spacing: 2px;
    color: var(--card-white);
  }
</style>
</head>
<body>
<div class="canvas">

  <section class="card card-front" aria-label="Business card front">
    <div class="brand-mark" aria-hidden="true"></div>
    <h1 class="brand-name">
      <span class="brand-main">TARWICK</span>
      <span class="brand-sub">TRADE SOLUTIONS LTD</span>
    </h1>
    <div class="contact">
      <p class="contact-name">DANIEL HARPER</p>
      <p class="contact-role">Managing Director</p>
      <div class="contact-rule"></div>
      <p class="contact-line">044-987 654 321</p>
      <p class="contact-line">hello@tarwickco.com</p>
      <div class="contact-rule"></div>
      <p class="contact-line">18, Harbour Street</p>
      <p class="contact-line">30117, Westmoor</p>
    </div>
  </section>

  <section class="card card-back" aria-label="Business card back">
    <svg class="back-art" width="369" height="594" viewBox="0 0 369 594" aria-hidden="true">
      <path class="back-lower-band" d="M0 185 C 18 440, 351 440, 369 185 L369 594 L0 594 Z" fill="#9bcb3c"/>
      <circle class="back-mark" cx="184" cy="310" r="62" fill="#ffffff"/>
    </svg>
    <p class="back-name">TARWICK</p>
  </section>

</div>
</body>
</html>
```